Bramblewood Card Company Business Cards

We are a trading card store with Glimmorax, sports and other TCG cards, we need a business card design that encompasses a clean cut, modern style with a retro flare. website is bramblewoodcardco.com for reference. Can utilize a comic book era feel or a more modern outdoor feel to utilize the "Pacific Northwest" elements of tress, mountains, etc.

Industry/Entity Type

Trading cards and collectibles

Contact Information for Business Card

business name, email address, phone number, name, owner job title

Font styles to use
Sans Serif

```html
<!DOCTYPE html>
<html lang="en">
<head>
<meta charset="utf-8">
<title>Bramblewood Card Company – Business Cards</title>
<link rel="stylesheet" href="https://fonts.googleapis.com/css2?family=Montserrat:wght@400;600;700&display=swap">
<style>
  :root {
    --sky: #14bde1;
    --slate: #6d6e70;
    --ink: #1f1f1f;
    --paper: #ffffff;
    --backdrop: #ece9e4;
  }
  * { box-sizing: border-box; margin: 0; padding: 0; }
  html, body { width: 1200px; height: 931px; overflow: hidden; }
  body {
    background: var(--backdrop);
    font-family: "Montserrat", sans-serif;
    position: relative;
  }
  .card {
    position: absolute;
    width: 700px;
    height: 400px;
    border-radius: 20px;
    overflow: hidden;
    box-shadow: 0 6px 18px rgba(0,0,0,0.18);
  }
  .card--back { left: 60px; top: 45px; background: var(--sky); }
  .card--front { left: 440px; top: 486px; background: var(--paper); }

  .brand {
    position: absolute;
    display: flex;
    align-items: center;
    gap: 14px;
    color: var(--slate);
    font-weight: 700;
    text-transform: uppercase;
    line-height: 1.15;
  }
  .brand__dot {
    flex: none;
    border-radius: 50%;
    background: var(--slate);
  }
  .card--back .brand { left: 0; right: 0; top: 150px; justify-content: center; font-size: 30px; }
  .card--back .brand__dot { width: 56px; height: 56px; }
  .card--front .brand { right: 44px; top: 70px; font-size: 22px; }
  .card--front .brand__dot { width: 42px; height: 42px; }

  .rule {
    position: absolute;
    left: 40px; right: 40px; top: 246px;
    height: 2px;
    background: var(--sky);
  }
  .person__name {
    position: absolute; left: 40px; top: 200px;
    color: var(--sky); font-weight: 700; font-size: 34px;
  }
  .person__role {
    position: absolute; left: 58px; top: 254px;
    color: var(--ink); font-size: 17px;
  }
  .contacts {
    position: absolute; left: 52px; top: 286px;
    list-style: none;
  }
  .contacts li {
    display: flex; align-items: center; gap: 12px;
    font-size: 16px; color: var(--ink); height: 25px;
  }
  .contacts svg { width: 16px; height: 16px; fill: var(--sky); flex: none; }
  .address {
    position: absolute; right: 44px; top: 292px;
    text-align: right; font-size: 15px; line-height: 1.45; color: var(--ink);
  }
  .bands { position: absolute; left: 0; bottom: 0; width: 700px; height: 40px; }
</style>
</head>
<body>

<section class="card card--back">
  <div class="brand">
    <span class="brand__dot"></span>
    <span>Bramblewood<br>Card Company</span>
  </div>
</section>

<section class="card card--front">
  <div class="brand">
    <span class="brand__dot"></span>
    <span>Bramblewood<br>Card Company</span>
  </div>

  <h1 class="person__name">Dorian Vale</h1>
  <div class="rule"></div>
  <p class="person__role">Owner</p>

  <ul class="contacts">
    <li>
      <svg viewBox="0 0 24 24"><path d="M6.6 10.8a15 15 0 0 0 6.6 6.6l2.2-2.2c.3-.3.7-.4 1-.2 1.1.4 2.3.6 3.6.6.6 0 1 .4 1 1V20c0 .6-.4 1-1 1A17 17 0 0 1 3 4c0-.6.4-1 1-1h3.5c.6 0 1 .4 1 1 0 1.3.2 2.5.6 3.6.1.3 0 .7-.2 1z"/></svg>
      06-48201937
    </li>
    <li>
      <svg viewBox="0 0 24 24"><path d="M2 5h20v14H2zM3.5 6.5 12 13l8.5-6.5z" fill-rule="evenodd"/></svg>
      info@bramblewoodcardcompany.com
    </li>
    <li>
      <svg viewBox="0 0 24 24"><path d="M12 2a10 10 0 1 0 0 20 10 10 0 0 0 0-20zm6.9 6h-3a15 15 0 0 0-1.3-3.9A8 8 0 0 1 18.9 8zM12 4c.8 1.2 1.5 2.5 1.9 4h-3.8c.4-1.5 1.1-2.8 1.9-4zM4.3 14a8 8 0 0 1 0-4h3.4a16 16 0 0 0 0 4zm.8 2h3a15 15 0 0 0 1.3 3.9A8 8 0 0 1 5.1 16zm3-8h-3a8 8 0 0 1 4.3-3.9C8.8 5.3 8.4 6.6 8.1 8zM12 20c-.8-1.2-1.5-2.5-1.9-4h3.8c-.4 1.5-1.1 2.8-1.9 4zm2.3-6H9.7a14 14 0 0 1 0-4h4.6a14 14 0 0 1 0 4zm.3 5.9c.6-1.2 1-2.5 1.3-3.9h3a8 8 0 0 1-4.3 3.9zM16.3 14a16 16 0 0 0 0-4h3.4a8 8 0 0 1 0 4z"/></svg>
      www.bramblewoodcardcompany.com
    </li>
  </ul>

  <p class="address">4820 Cedar Hollow Ave Suite118<br>Millbrook, Ohio 44092</p>

  <svg class="bands" viewBox="0 0 700 40" preserveAspectRatio="none">
    <polygon points="0,22 520,22 510,40 0,40" fill="var(--slate)"/>
    <polygon points="532,0 700,0 700,40 520,40" fill="var(--sky)"/>
  </svg>
</section>

</body>
</html>
```